business card design for a plumbing contractor

i need a double business card for a plumbing business, our initial service is residential Sewer Drain Cleaning.

Target Market(s)

other plumbing Business

Industry/Entity Type

Plumbing

Contact Information for Business Card

www.PipeworksTopMark.example- 5307218394-

Font styles to use
Serif

Colors
ec1f27
0455a3

```html
<!DOCTYPE html>
<html lang="en">
<head>
<meta charset="utf-8">
<title>Pipeworks Top Mark — Business Card</title>
<link href="https://fonts.googleapis.com/css2?family=Roboto+Condensed:wght@400;700&display=swap" rel="stylesheet">
<style>
  :root {
    --backdrop: #2a2a2a;
    --card-white: #f4f4f3;
    --brand-red: #d8372f;
    --warm-grey: #7d7467;
    --ink: #3c3c3c;
  }
  * { margin: 0; padding: 0; box-sizing: border-box; }
  html, body { width: 1200px; height: 960px; overflow: hidden; }
  body {
    background: var(--backdrop);
    font-family: "Roboto Condensed", Arial, sans-serif;
    position: relative;
  }
  .card {
    position: absolute;
    left: 320px;
    width: 600px;
    height: 344px;
    box-shadow: 0 3px 8px rgba(0,0,0,.45);
  }
  .card-front { top: 100px; background: var(--card-white); }
  .card-back { top: 493px; background: var(--brand-red); display: flex; align-items: center; justify-content: center; }

  .brand-lockup {
    position: absolute;
    left: 34px;
    top: 44px;
    display: flex;
    align-items: center;
    gap: 12px;
  }
  .brand-name {
    font-weight: 700;
    font-size: 34px;
    line-height: 1;
    color: var(--warm-grey);
  }
  .brand-square {
    width: 22px; height: 22px;
    background: var(--brand-red);
  }

  .contact-block {
    position: absolute;
    right: 28px;
    top: 222px;
    text-align: right;
  }
  .person-name {
    font-weight: 700;
    font-size: 22px;
    color: var(--brand-red);
    line-height: 1.1;
  }
  .person-title {
    font-weight: 700;
    font-size: 15px;
    color: var(--warm-grey);
    margin-bottom: 16px;
  }
  .contact-line {
    display: flex;
    justify-content: flex-end;
    align-items: center;
    gap: 6px;
    font-size: 14px;
    color: var(--ink);
    line-height: 18px;
  }
  .contact-icon { width: 12px; height: 12px; fill: var(--brand-red); }

  .back-name {
    font-weight: 700;
    font-size: 46px;
    color: #ffffff;
    text-align: center;
    line-height: 1.1;
  }
</style>
</head>
<body>
  <section class="card card-front">
    <div class="brand-lockup">
      <span class="brand-name">Pipeworks Top Mark</span>
      <span class="brand-square"></span>
    </div>
    <div class="contact-block">
      <div class="person-name">MARCUS HALE</div>
      <div class="person-title">CEO/FOUNDER</div>
      <div class="contact-line">5307218394
        <svg class="contact-icon" viewBox="0 0 24 24"><path d="M6.6 10.8a15.1 15.1 0 0 0 6.6 6.6l2.2-2.2a1 1 0 0 1 1-.25 11.4 11.4 0 0 0 3.6.57 1 1 0 0 1 1 1V20a1 1 0 0 1-1 1A17 17 0 0 1 3 4a1 1 0 0 1 1-1h3.5a1 1 0 0 1 1 1c0 1.25.2 2.45.57 3.57a1 1 0 0 1-.25 1z"/></svg>
      </div>
      <div class="contact-line">Dispatch@PipeworksTopMark.example
        <svg class="contact-icon" viewBox="0 0 24 24"><path d="M2 5h20v14H2z M2 5l10 7 10-7" fill="none" stroke="#d8372f" stroke-width="0"/><path d="M2 5h20v2l-10 7L2 7z"/><path d="M2 9l10 7 10-7v10H2z"/></svg>
      </div>
      <div class="contact-line">www.PipeworksTopMark.example
        <svg class="contact-icon" viewBox="0 0 24 24"><circle cx="12" cy="12" r="11"/><path d="M7 8c2 0 3 1 3 3s-2 2-2 4M14 4c0 2 2 2 3 4s-1 3 0 5 3 1 3 1" fill="none" stroke="#f4f4f3" stroke-width="1.6"/></svg>
      </div>
    </div>
  </section>

  <section class="card card-back">
    <div class="back-name">Pipeworks<br>Top Mark</div>
  </section>
</body>
</html>
```